Product Design for VelaMira

Design Brief for VelaMira Product Packaging

Objective:
Create a cohesive, elegant, and brand-consistent packaging design for the VelaMira product line. The signature visual theme should reflect luxury, femininity, and clean beauty values.

---

🎨 Core Design Direction

Unified Aesthetic: All containers must prominently feature the floral pattern shown in "Pattern Reference: Image 3". This design serves as the brand's signature aesthetic and must be applied uniformly across all SKUs.

Brand Logo Placement: The VelaMira logo (provided) should be clearly visible and harmoniously integrated into the patterned background.

Color Palette: Base colors should complement the brand’s primary palette: black, blush pink, and white.

---

🧴 Product-Specific Packaging Specifications

1. Mascara

Bottle Type: Sleek mascara tube with a wand applicator

Capacity: 5ml

Design: Use floral pattern from Pattern Reference Image 3. Ensure the pattern does not obstruct the readability of the logo or any regulatory text.

2. Eyebrow Growth Serum

Bottle Type: 5ml tube with fine-tip brush applicator

Capacity: 5ml

Design: Same floral pattern, scaled and applied proportionally to match the mascara for consistency

3. Eyelash Growth Serum

Bottle Type: 5ml tube with fine-tip brush (similar to the eyebrow serum, unless otherwise advised)

Capacity: 5ml

Design: Identical styling to maintain unity across lash & brow products

4. Anti-Aging Serum or Lotion

Bottle Type: 30ml airless pump bottle (preferred for hygiene and product stability)

Capacity: 30ml

Design: Apply floral pattern from Pattern Reference and scale appropriately for larger surface area

5. Hair Growth Spray

Bottle Type: 50ml fine mist spray bottle

Capacity: 50ml

Design: Pattern applied and scaled for taller profile; maintain visual harmony with skincare line

---

📦 Additional Notes

Please ensure packaging aligns with clean beauty standards (no overly glossy plastic finishes, avoid excessive secondary packaging unless sustainable).

Materials should be eco-conscious where possible.

If embossing, foil stamping, or UV finishing is available for logo accents, please suggest options.

```html
<!DOCTYPE html>
<html lang="en">
<head>
<meta charset="utf-8">
<title>VelaMira Eyebrow Growth Serum Label</title>
<link href="https://fonts.googleapis.com/css2?family=Lato:wght@400;700&display=swap" rel="stylesheet">
<style>
  :root {
    --canvas: #e3e4e4;
    --ink: #0c0c0c;
    --cream: #f3ede0;
    --peach: #e59a76;
    --blush-light: #fdf7f3;
    --blush: #f4cdb9;
  }
  * { margin: 0; padding: 0; box-sizing: border-box; }
  html, body { width: 1200px; height: 1200px; overflow: hidden; }
  body {
    background: var(--canvas);
    font-family: "Lato", sans-serif;
    color: var(--cream);
    position: relative;
  }
  .label {
    position: absolute;
    left: 252px; top: 100px;
    width: 695px; height: 1000px;
  }
  .floral-field {
    position: absolute; inset: 0;
    background:
      radial-gradient(circle at 25% 20%, var(--blush) 0, transparent 30%),
      radial-gradient(circle at 75% 60%, var(--blush) 0, transparent 32%),
      radial-gradient(circle at 40% 90%, var(--blush) 0, transparent 28%),
      var(--blush-light);
  }
  .strip {
    position: absolute;
    top: 92px; width: 151px; height: 817px;
    background: var(--ink);
    text-align: center;
  }
  .strip--front { left: 98px; }
  .strip--back { left: 445px; }

  .brand-name {
    position: absolute;
    left: 0; right: 0; top: 40px; height: 440px;
    display: flex; align-items: center; justify-content: center;
  }
  .brand-name span {
    writing-mode: vertical-rl;
    transform: rotate(180deg);
    font-size: 74px; font-weight: 400;
    letter-spacing: 1px;
    color: var(--cream);
  }
  .product-title {
    position: absolute; left: 0; right: 0; top: 552px;
    font-size: 26px; font-weight: 700; line-height: 1.1;
  }
  .product-claim {
    position: absolute; left: 0; right: 0; top: 668px;
    font-size: 20px; line-height: 1.3;
  }
  .product-volume {
    position: absolute; left: 0; right: 0; top: 748px;
    font-size: 20px; line-height: 1.3;
  }

  .ingredients { padding-top: 42px; font-size: 22px; line-height: 1.28; }
  .ingredients strong, .caution strong { font-weight: 700; display: block; }
  .caution { margin-top: 22px; font-size: 22px; line-height: 1.3; }
  .claims { margin-top: 60px; list-style: none; }
  .claim { display: flex; flex-direction: column; align-items: center; margin-bottom: 14px; }
  .claim svg { width: 54px; height: 54px; }
  .claim-text { margin-top: 4px; font-size: 11px; font-weight: 700; color: var(--peach); }
  .distributor { margin-top: 12px; font-size: 20px; line-height: 1.4; }
  .distributor strong { font-weight: 700; }
</style>
</head>
<body>
  <section class="label">
    <div class="floral-field" role="img" aria-label="Blush peach floral pattern of blossoms and leaves on a soft white ground"></div>

    <div class="strip strip--front">
      <div class="brand-name"><span>VelaMira</span></div>
      <h1 class="product-title">Eyebrow<br>Growth<br>Serum</h1>
      <p class="product-claim">Thicker +<br>Fuller Brows</p>
      <p class="product-volume">5ml/<br>0.17 fl.oz.</p>
    </div>

    <div class="strip strip--back">
      <p class="ingredients"><strong>Ingredients:</strong>Aqua, Biotin,<br>Panthenol,<br>Polysorbate<br>20</p>
      <p class="caution"><strong>Caution:</strong>For external<br>use only.</p>
      <ul class="claims">
        <li class="claim">
          <svg viewBox="0 0 54 54" fill="none" stroke="var(--peach)" stroke-width="2.4" stroke-linecap="round">
            <circle cx="27" cy="27" r="24"/>
            <path d="M23 15v9l-7 13h22l-7-13v-9M21 15h12"/>
            <path d="M12 12l30 30"/>
          </svg>
          <span class="claim-text">Paraben Free</span>
        </li>
        <li class="claim">
          <svg viewBox="0 0 54 54" fill="none" stroke="var(--peach)" stroke-width="2.4" stroke-linecap="round" stroke-linejoin="round">
            <circle cx="27" cy="27" r="24"/>
            <path d="M17 28l7 7 13-15"/>
          </svg>
          <span class="claim-text">Dermatologist Tested</span>
        </li>
        <li class="claim">
          <svg viewBox="0 0 54 54" fill="none" stroke="var(--peach)" stroke-width="2.4" stroke-linecap="round" stroke-linejoin="round">
            <circle cx="27" cy="27" r="24"/>
            <path d="M27 13c-7 9-10 14-10 19a10 10 0 0 0 20 0c0-5-3-10-10-19z"/>
            <path d="M27 24v16M27 32l-4-4M27 30l4-4"/>
          </svg>
          <span class="claim-text">Strengthens Roots</span>
        </li>
        <li class="claim">
          <svg viewBox="0 0 54 54" fill="none" stroke="var(--peach)" stroke-width="2.4" stroke-linecap="round" stroke-linejoin="round">
            <circle cx="27" cy="27" r="24"/>
            <path d="M27 13c-7 9-10 14-10 19a10 10 0 0 0 20 0c0-5-3-10-10-19z"/>
          </svg>
          <span class="claim-text">Cruelty Free</span>
        </li>
      </ul>
      <p class="distributor">Distributed by<br><strong>VelaMira</strong>,<br>London, UK</p>
    </div>
  </section>
</body>
</html>
```